Tolvane Inc., a third party debt collection agency needs a Website

Tolvane needs a very basic website (3 basic pages) so that consumers can download forms, potential employees can get required EEO language and see potential jobs, and to show that they are a consumer friendly organization.

I've attached a list of requirements and wishes titled "Tolvane Website Specifications"

Target Market(s)

Consumers that need to repay their government loans; Tolvane will walk through the process to assist them.

Industry/Entity Type

Financial Service

Coding

Coded - Design and coding required

Number of Pages Required

1 page

Font styles to use
Sans Serif

Colors
0355a3

Requirements
Must have
• Tolvane Logo
• See document "Tolvane Website Specifications" for all requirements

```html
<!DOCTYPE html>
<html lang="en">
<head>
<meta charset="utf-8">
<title>Tolvane Inc.</title>
<link rel="stylesheet" href="https://fonts.googleapis.com/css2?family=Roboto+Condensed:wght@400;700&family=Open+Sans:wght@400;700&display=swap">
<style>
  :root {
    --navy: #25286f;
    --crimson: #8b1a1a;
    --ink: #555a60;
    --mist: #e6e6e6;
    --line: #cfcfcf;
    --white: #ffffff;
  }
  * { margin: 0; padding: 0; box-sizing: border-box; }
  html, body { width: 1200px; height: 2264px; overflow: hidden; }
  body {
    position: relative;
    background: var(--white);
    font-family: "Open Sans", Arial, sans-serif;
    color: var(--ink);
  }
  .abs { position: absolute; }
  .cond { font-family: "Roboto Condensed", "Arial Narrow", sans-serif; }

  /* Hero */
  .hero { left: 0; top: 0; width: 1200px; height: 717px; overflow: hidden; }
  .hero-photo {
    position: absolute; inset: 0;
    background:
      radial-gradient(ellipse 420px 520px at 380px 420px, #b8a590 0%, rgba(184,165,144,0) 70%),
      linear-gradient(100deg, #e9e4da 0%, #f3f1ec 40%, #f7f6f2 60%, #d9c8ad 100%);
  }
  .brand {
    left: 75px; top: 58px;
    font-family: "Roboto Condensed", sans-serif; font-weight: 700;
    font-size: 34px; color: var(--crimson); letter-spacing: 0.2px;
  }
  .nav { top: 57px; height: 50px; display: flex; align-items: center; }
  .nav a {
    position: absolute; top: 0; height: 50px; line-height: 50px;
    font-family: "Roboto Condensed", sans-serif; font-size: 20px;
    color: #2b2b2b; text-decoration: none; white-space: nowrap;
  }
  .nav a.is-active {
    background: var(--navy); color: var(--white);
    border-radius: 3px; width: 98px; text-align: center;
  }
  .hero-title {
    right: 80px; top: 248px; text-align: right;
    font-family: "Roboto Condensed", sans-serif; font-size: 42px;
    line-height: 63px; color: var(--navy); font-weight: 400;
  }
  .hero-button {
    left: 726px; top: 409px; width: 397px; height: 62px;
    background: var(--crimson); color: var(--white); border-radius: 4px;
    font-family: "Roboto Condensed", sans-serif; font-size: 23px;
    line-height: 62px; text-align: center;
  }

  /* Advice band */
  .advice { left: 0; top: 717px; width: 1200px; height: 155px; background: var(--navy); color: var(--white); }
  .advice-note { left: 80px; top: 41px; width: 520px; font-family: "Roboto Condensed", sans-serif; font-size: 20px; line-height: 31px; }
  .advice-rule { left: 635px; top: 42px; width: 1px; height: 71px; background: rgba(255,255,255,0.8); }
  .advice-label { left: 693px; top: 56px; font-family: "Roboto Condensed", sans-serif; font-size: 31px; line-height: 40px; }
  .advice-icon { left: 871px; top: 44px; }
  .advice-number { left: 947px; top: 54px; font-family: "Roboto Condensed", sans-serif; font-weight: 700; font-size: 34px; line-height: 44px; }

  /* Welcome */
  .section-title {
    left: 0; width: 1200px; text-align: center;
    font-family: "Roboto Condensed", sans-serif; font-size: 44px;
    color: var(--navy); font-weight: 400;
  }
  .section-title em { font-style: normal; color: var(--crimson); }
  .welcome-title { top: 918px; }
  .welcome-text { left: 150px; top: 988px; width: 900px; text-align: center; font-size: 16px; line-height: 25.5px; }
  .tree-brand {
    left: 0; top: 1150px; width: 1200px; text-align: center;
    font-family: "Roboto Condensed", sans-serif; font-weight: 700;
    font-size: 33px; color: var(--crimson);
  }
  .tree { left: 0; top: 1230px; }
  .tree-node {
    width: 146px; height: 146px; border-radius: 50%;
    border: 1.5px solid var(--line); background: var(--white);
    display: flex; align-items: center; justify-content: center; text-align: center;
    font-family: "Roboto Condensed", sans-serif; font-size: 19px; line-height: 25px;
  }
  .tree-node.consumer { left: 241px; top: 1364px; color: var(--navy); }
  .tree-node.career { left: 813px; top: 1364px; color: var(--crimson); }

  /* Testimonials */
  .reviews { left: 0; top: 1574px; width: 1200px; height: 365px; background: var(--mist); }
  .reviews-title { top: 40px; }
  .review-arrow { top: 165px; }
  .review-avatar {
    left: 160px; top: 127px; width: 124px; height: 124px; border-radius: 50%;
    border: 2px solid var(--navy);
    background: radial-gradient(circle at 50% 40%, #c9b8a6 0%, #8e8c93 55%, #3d4150 100%);
  }
  .review-text { left: 302px; top: 134px; width: 730px; font-size: 16px; line-height: 26px; }
  .review-name { left: 302px; top: 212px; font-size: 15px; font-weight: 700; color: var(--crimson); }
  .review-dots { left: 173px; top: 285px; }

  /* Footer */
  .footer { left: 0; top: 1939px; width: 1200px; height: 272px; background: var(--navy); color: var(--white); }
  .footer-heading { top: 33px; font-family: "Roboto Condensed", sans-serif; font-size: 26px; }
  .footer-links { left: 80px; top: 83px; list-style: none; font-size: 17px; line-height: 36.3px; }
  .badge-member { left: 350px; top: 78px; }
  .badge-accredit { left: 617px; top: 75px; }
  .social { left: 888px; top: 69px; }

  .copyright {
    left: 0; top: 2211px; width: 1200px; height: 53px; background: var(--crimson);
    color: var(--white); text-align: center; font-size: 16px; line-height: 53px;
  }
</style>
</head>
<body>

<header class="abs hero">
  <div class="hero-photo" role="img" aria-label="Smiling woman working on a laptop at a bright office desk"></div>
  <div class="abs brand">Tolvane Inc.</div>
  <nav class="abs nav" style="left:0;">
    <a class="is-active" href="#" style="left:543px;">HOME</a>
    <a href="#" style="left:660px;">CONSUMER INFORMATION</a>
    <a href="#" style="left:927px;">CAREER</a>
    <a href="#" style="left:1038px;">CONTACT</a>
  </nav>
  <h1 class="abs hero-title">ASSIST CONSUMERS IN<br>RESOLVING THEIR OBLIGATIONS</h1>
  <div class="abs hero-button">EMPLOYMENT APPLICATION FORM</div>
</header>

<section class="abs advice">
  <p class="abs advice-note">Best meets their needs and to provide information necessary in order for consumers to make an informed decision.</p>
  <div class="abs advice-rule"></div>
  <div class="abs advice-label">FREE ADVICE</div>
  <svg class="abs advice-icon" width="62" height="62" viewBox="0 0 62 62" aria-hidden="true">
    <circle cx="31" cy="31" r="30" fill="none" stroke="#fff" stroke-width="1.5"/>
    <path d="M23 20c1.5-1 3-1 3.8.3l2.6 4c.7 1.1.4 2.3-.6 3l-1.7 1.2c.9 2.4 3 4.7 5.4 6l1.3-1.6c.8-1 2-1.2 3-.5l3.9 2.7c1.2.8 1.2 2.4.2 3.7l-1.6 1.9c-1.4 1.6-4.5 1.6-8.4-.8-4.9-3.1-8.8-8-10.2-12.4-.9-2.9-.3-5.6 1.3-6.9z" fill="#fff"/>
  </svg>
  <div class="abs advice-number">555 204 7731</div>
</section>

<h2 class="abs section-title welcome-title">WELCOME TO <em>TOLVANE INC.</em></h2>
<p class="abs welcome-text">Tolvane is a third party debt collection agency that is focused on the collection of higher education loans.&nbsp; Tolvane is compliant with all federal, state, and local laws and is committed to the professional and fair treatment of consumers.&nbsp; Our goal is to assist consumers in resolving their obligations in the manner that best meets their needs and to provide information necessary in order for consumers to make an informed decision.</p>

<div class="abs tree-brand">Tolvane Inc.</div>
<svg class="abs tree" width="1200" height="140" viewBox="0 0 1200 140" aria-hidden="true">
  <path d="M599.5 4V68M314.5 68H886.5M314.5 68V136M886.5 68V136" fill="none" stroke="#cfcfcf" stroke-width="1.5"/>
</svg>
<div class="abs tree-node consumer">CONSUMER<br>INFORMATION</div>
<div class="abs tree-node career">CAREER</div>

<section class="abs reviews">
  <h2 class="abs section-title reviews-title">WHAT OUR <em>CLIENT SAY</em></h2>
  <svg class="abs review-arrow" style="left:114px;" width="20" height="48" viewBox="0 0 20 48" aria-hidden="true"><path d="M17 2L3 24l14 22" fill="none" stroke="#25286f" stroke-width="2"/></svg>
  <svg class="abs review-arrow" style="left:1070px;" width="20" height="48" viewBox="0 0 20 48" aria-hidden="true"><path d="M3 2l14 22L3 46" fill="none" stroke="#25286f" stroke-width="2"/></svg>
  <div class="abs review-avatar" role="img" aria-label="Portrait photo of the client"></div>
  <p class="abs review-text">Lorem Ipsum is simply dummy text of the printing and typesetting industry. Lorem Ipsum has been the industry's standard dummy text ever since the 1500.</p>
  <div class="abs review-name">- CLIENT NAME</div>
  <svg class="abs review-dots" width="84" height="18" viewBox="0 0 84 18" aria-hidden="true">
    <circle cx="8" cy="9" r="7" fill="#25286f"/>
    <circle cx="40" cy="9" r="6.5" fill="none" stroke="#25286f" stroke-width="1.5"/>
    <circle cx="71" cy="9" r="6.5" fill="none" stroke="#25286f" stroke-width="1.5"/>
  </svg>
</section>

<footer class="abs footer">
  <div class="abs footer-heading" style="left:80px;">Useful Links</div>
  <div class="abs footer-heading" style="left:350px;">Member</div>
  <div class="abs footer-heading" style="left:620px;">Accrediation</div>
  <div class="abs footer-heading" style="left:890px;">Follow Us</div>
  <ul class="abs footer-links">
    <li>Home</li>
    <li>Consumer Information</li>
    <li>Career</li>
    <li>Discloser</li>
  </ul>
  <svg class="abs badge-member" width="142" height="156" viewBox="0 0 142 156" role="img" aria-label="Member association badge">
    <rect x="22" y="2" width="98" height="150" rx="4" fill="#fff" opacity="0.9"/>
  </svg>
  <svg class="abs badge-accredit" width="112" height="162" viewBox="0 0 112 162" role="img" aria-label="Accreditation badge">
    <rect x="2" y="2" width="108" height="156" rx="4" fill="#fff" opacity="0.9"/>
  </svg>
  <svg class="abs social" width="200" height="56" viewBox="0 0 200 56" role="img" aria-label="Social media links">
    <circle cx="26" cy="26" r="25" fill="#fff"/>
    <circle cx="99" cy="26" r="25" fill="none" stroke="#fff" stroke-width="1.5"/>
    <circle cx="171" cy="26" r="25" fill="none" stroke="#fff" stroke-width="1.5"/>
  </svg>
</footer>

<div class="abs copyright">© Tolvane Inc. - 2016. All Rights Reserved.</div>

</body>
</html>
```